Oil and Gas Exploration and Production company needs a business card design

We need a business card design using our logo and colors in the logo. We want a mainstream design.

```html
<!DOCTYPE html>
<html lang="en">
<head>
<meta charset="UTF-8">
<title>Ridgeline Oil &amp; Gas — Business Card</title>
<link rel="stylesheet" href="https://fonts.googleapis.com/css2?family=Work+Sans:wght@400;500;600&display=swap">
<style>
  :root {
    --backdrop: #2b2b2d;
    --card: #1c1c1d;
    --ink-white: #f2f2f2;
    --ink-soft: #e4e4e4;
    --gold: #d9a223;
    --emboss: #3a3a3c;
    --emboss-light: #8d8d90;
  }
  * { box-sizing: border-box; margin: 0; padding: 0; }
  html, body {
    width: 1200px; height: 900px; overflow: hidden;
    background: var(--backdrop);
    font-family: "Work Sans", Arial, sans-serif;
  }
  .canvas {
    width: 1200px; height: 900px;
    display: flex; flex-direction: column; align-items: center; justify-content: center;
    gap: 30px;
  }
  .card {
    position: relative;
    width: 700px; height: 400px;
    background: var(--card);
    box-shadow: 0 10px 30px rgba(0,0,0,0.45);
  }
  /* Front */
  .card-front { display: flex; align-items: center; justify-content: center; }
  .brand { display: flex; align-items: center; gap: 14px; }
  .brand-dot { width: 30px; height: 30px; border-radius: 50%; }
  .brand-name { font-weight: 600; letter-spacing: 0.5px; }
  .card-front .brand-dot { background: var(--emboss-light); }
  .card-front .brand-name { font-size: 48px; color: var(--emboss-light); }

  /* Back */
  .card-back .brand { position: absolute; left: 48px; top: 48px; }
  .card-back .brand-dot { width: 22px; height: 22px; background: var(--ink-white); }
  .card-back .brand-name { font-size: 34px; color: var(--ink-white); }
  .person { position: absolute; left: 48px; top: 140px; }
  .person-name { font-size: 30px; font-weight: 500; color: var(--gold); }
  .person-role { font-size: 15px; color: var(--ink-soft); margin-top: 2px; }
  .address { position: absolute; left: 48px; top: 222px; font-size: 16px; line-height: 1.45; color: var(--ink-soft); }
  .contacts { position: absolute; left: 48px; top: 292px; list-style: none; font-size: 16px; color: var(--ink-soft); }
  .contacts li { display: flex; align-items: center; gap: 10px; line-height: 1.55; }
  .contacts svg { width: 12px; height: 12px; flex: none; }
  .highlight { color: var(--gold); }
  .emblem { position: absolute; right: 70px; top: 85px; width: 230px; height: 230px; }
</style>
</head>
<body>
<main class="canvas">
  <section class="card card-front" aria-label="Card front">
    <div class="brand">
      <span class="brand-dot"></span>
      <span class="brand-name">Ridgeline Oil &amp; Gas</span>
    </div>
  </section>

  <section class="card card-back" aria-label="Card back">
    <div class="brand">
      <span class="brand-dot"></span>
      <span class="brand-name">Ridgeline Oil &amp; Gas</span>
    </div>

    <div class="person">
      <p class="person-name">Dale Hensley</p>
      <p class="person-role">CFO</p>
    </div>

    <p class="address">2450 W Ridge Ave,<br>Abilene, Texas us</p>

    <ul class="contacts">
      <li>
        <svg viewBox="0 0 12 12" aria-hidden="true"><path d="M3 1 L5 3.5 L4 4.8 Q5 7 7.2 8 L8.5 7 L11 9 L9.8 11 Q4.5 10.5 1 3.2 Z" fill="var(--gold)"/></svg>
        (555) 014-2278
      </li>
      <li>
        <svg viewBox="0 0 12 12" aria-hidden="true"><rect x="1" y="2.5" width="10" height="7" fill="none" stroke="var(--gold)" stroke-width="1.2"/><path d="M1 2.5 L6 6.5 L11 2.5" fill="none" stroke="var(--gold)" stroke-width="1.2"/></svg>
        info@ridgelineoil.com
      </li>
      <li>
        <svg viewBox="0 0 12 12" aria-hidden="true"><circle cx="6" cy="6" r="5" fill="none" stroke="var(--gold)" stroke-width="1.1"/><path d="M1 6 H11 M6 1 V11" stroke="var(--gold)" stroke-width="1"/></svg>
        <span>www.<span class="highlight">ridgelineoil</span>.com</span>
      </li>
    </ul>

    <svg class="emblem" viewBox="0 0 230 230" aria-hidden="true">
      <defs>
        <linearGradient id="emboss-sheen" x1="0" y1="0" x2="1" y2="1">
          <stop offset="0" stop-color="var(--emboss)"/>
          <stop offset="1" stop-color="var(--emboss-light)"/>
        </linearGradient>
      </defs>
      <circle cx="115" cy="115" r="95" fill="none" stroke="url(#emboss-sheen)" stroke-width="14"/>
    </svg>
  </section>
</main>
</body>
</html>
```